We are building a website where users come to see what skills they will need for their career. The content of the page is data-driven, so the site should have the feel of a set of data dashboards. The data is collected and processed using machine learning. The main idea is for the user to come in and spend some minutes exploring, scrolling and clicking around.
The task is to design a website with four pages:
Front page
Early career page
Skill trends page
Skills Page
Each of these is described in attached files, along with example data
We need the resulting files to be exported also to uncompressed PNG, and in the case of vector graphics, to SVG.
Target Market(s)
People Looking to start a Career and Policy makers.
Industry/Entity Type
Human Resource
Number of Pages Required
4 page
Look and feel

```html
<!DOCTYPE html>
<html lang="en">
<head>
<meta charset="utf-8">
<title>SKILLPATH – Your personal guide to the skill trends on the job market</title>
<link rel="stylesheet" href="https://fonts.googleapis.com/css2?family=Arimo:wght@400;700&family=Lato:wght@400;700&display=swap">
<style>
:root{
  --navy:#0d3f86;
  --blue:#1553a8;
  --band:#124a9b;
  --ink:#111111;
  --text:#333333;
  --muted:#555555;
  --light:#f4f4f4;
  --white:#ffffff;
  --footer:#151515;
}
*{box-sizing:border-box;margin:0;padding:0}
html,body{width:1200px;height:4142px;overflow:hidden;background:var(--white)}
body{font-family:"Lato",Arial,sans-serif;color:var(--text);position:relative}
.heading{font-family:"Arimo",Arial,sans-serif;font-weight:700;color:var(--ink);text-transform:uppercase}
.btn{display:flex;align-items:center;justify-content:center;font-family:"Arimo",Arial,sans-serif;font-weight:700;font-size:15px;color:var(--white);background:linear-gradient(180deg,#1c5fb8,var(--navy));border-radius:3px;text-transform:uppercase}

/* header */
.site-header{position:absolute;left:0;top:0;width:1200px;height:65px;background:var(--white)}
.brand{position:absolute;left:112px;top:15px;display:flex;align-items:center;gap:10px;font-family:"Arimo",Arial,sans-serif;font-weight:700;font-size:29px;color:var(--ink)}
.brand-mark{width:30px;height:30px;border-radius:50%;background:var(--blue)}
.main-nav{position:absolute;right:111px;top:24px;display:flex;font-family:"Arimo",Arial,sans-serif;font-weight:700;font-size:16px;color:var(--ink)}
.main-nav .sep{margin:0 27px;color:#444}
.main-nav .active{color:var(--navy)}

/* hero */
.hero{position:absolute;left:0;top:65px;width:1200px;height:605px;background:
  radial-gradient(ellipse 420px 360px at 780px 230px,rgba(150,200,255,.55),rgba(60,120,210,.25) 55%,transparent 80%),
  linear-gradient(90deg,#10192c 0%,#1a2f55 35%,#2a5aa0 65%,#2d5c9c 85%,#1c3c70 100%)}
.hero-title{position:absolute;left:129px;top:198px;font-family:"Arimo",Arial,sans-serif;font-weight:700;font-size:72px;line-height:80px;color:var(--white);letter-spacing:1px}
.hero-sub{position:absolute;left:129px;top:281px;width:400px;font-family:"Arimo",Arial,sans-serif;font-weight:700;font-size:19px;line-height:26px;color:var(--white)}
.hero .btn{position:absolute;left:129px;top:355px;width:150px;height:40px}
.hero-arrow{position:absolute;top:280px}
.dots{position:absolute;left:565px;top:560px;display:flex;gap:8px}
.dots i{display:block;width:10px;height:10px;border-radius:50%;background:rgba(255,255,255,.5)}
.dots i:first-child{background:var(--white)}

/* main goal */
.goal{position:absolute;left:0;top:670px;width:1200px;height:528px;background:var(--white)}
.goal-photo{position:absolute;left:137px;top:85px;width:421px;height:358px;background:linear-gradient(120deg,#4a3a30 0%,#8a6a55 30%,#c9c0b6 55%,#7d8a96 80%,#3d4652 100%)}
.frame-tl{position:absolute;left:120px;top:68px;width:86px;height:86px;border-left:4px solid var(--navy);border-top:4px solid var(--navy)}
.frame-br{position:absolute;left:488px;top:366px;width:86px;height:92px;border-right:4px solid var(--navy);border-bottom:4px solid var(--navy)}
.goal-copy{position:absolute;left:654px;top:102px;width:428px}
.goal-copy h2{font-size:40px;line-height:46px}
.goal-copy p{margin-top:24px;font-size:13.6px;line-height:26.5px;text-align:justify;color:var(--muted)}
.goal-copy .btn{margin-top:18px;width:150px;height:42px}

/* three ways */
.ways{position:absolute;left:0;top:1198px;width:1200px;height:378px;background:linear-gradient(180deg,#1a57ad,var(--band) 60%,#0f418e)}
.ways h2{position:absolute;left:0;top:60px;width:1200px;text-align:center;font-size:36px;color:var(--white)}
.card{position:absolute;top:152px;background:var(--white);border-radius:2px}
.search-card{left:111px;width:315px;height:70px}
.search-field{position:absolute;left:10px;top:10px;width:293px;height:50px;border:1px solid #ccc;border-radius:3px;font-size:13px;color:#555;padding:16px 20px;display:flex;justify-content:space-between}
.ad-card{left:443px;width:314px;height:162px;padding:5px 6px;font-size:8.4px;line-height:13.6px;color:#222;font-family:Arial,sans-serif;overflow:hidden}
.tag{display:inline-block;border:1px solid #4866d6;color:#3a55c8;padding:0 5px;line-height:11px;border-radius:2px;margin:0 1px}
.chart-card{left:775px;width:314px;height:111px}

/* intro */
.intro{position:absolute;left:0;top:1576px;width:1200px;height:1222px;background:var(--light)}
.intro>h2{position:absolute;left:0;top:80px;width:1200px;text-align:center;font-size:35px}
.intro-photo{position:absolute}
.challenges{position:absolute;left:111px;top:228px;width:440px}
.challenges h3,.method h3{font-size:30px;margin-bottom:12px}
.challenges p,.method p{font-size:14.5px;line-height:26.5px;color:var(--text);margin-bottom:8px}
.method{position:absolute;left:641px;top:735px;width:450px}

/* about */
.about{position:absolute;left:0;top:2798px;width:1200px;height:972px;background:linear-gradient(180deg,#1e55a8,#113f8d 40%,#123f86)}
.about h2{position:absolute;left:0;top:80px;width:1200px;text-align:center;font-size:38px;color:var(--white)}
.about-text{position:absolute;left:120px;top:138px;width:960px;text-align:center;color:var(--white);font-size:14px;line-height:25.8px}
.about-text p{margin-bottom:10px}
.about-text a{color:var(--white)}
.member{position:absolute;top:348px;width:315px;text-align:center;color:var(--white)}
.member-photo{width:315px;height:322px}
.member h4{font-family:"Arimo",Arial,sans-serif;font-weight:700;font-size:19px;margin-top:15px}
.member p{font-size:13px;line-height:25.5px;margin-top:4px}
.socials{display:flex;justify-content:center;gap:16px;margin-top:14px}
.socials i{display:block;width:13px;height:13px;border-radius:50%;background:var(--white)}
.donate{position:absolute;left:526px;top:856px;width:148px;height:40px;border:1px solid rgba(255,255,255,.8);border-radius:3px;color:var(--white);font-family:"Arimo",Arial,sans-serif;font-weight:700;font-size:15px;display:flex;align-items:center;justify-content:center}

/* footer */
.site-footer{position:absolute;left:0;top:3770px;width:1200px;height:372px;background:var(--footer);color:var(--white)}
.foot-brand{position:absolute;left:111px;top:70px;width:155px;text-align:center}
.foot-brand .brand-mark{width:48px;height:48px;margin:0 auto 16px;background:var(--white)}
.foot-brand span{font-family:"Arimo",Arial,sans-serif;font-weight:700;font-size:28px}
.foot-col h5{font-family:"Arimo",Arial,sans-serif;font-weight:700;font-size:20px;margin-bottom:12px}
.links{position:absolute;left:356px;top:76px}
.links li{list-style:none;font-size:15px;line-height:29.5px}
.newsletter{position:absolute;left:585px;top:76px;width:270px}
.newsletter .field{width:270px;height:44px;background:var(--white);color:#666;font-size:13px;padding:14px 12px}
.newsletter .subscribe{margin-top:8px;width:270px;height:44px;background:linear-gradient(180deg,#1c5fb8,var(--navy));display:flex;align-items:center;justify-content:center;font-size:16px}
.round{display:inline-block;width:36px;height:36px;border:2px solid var(--white);border-radius:50%;margin:22px 6px 0 3px}
.powered{position:absolute;left:943px;top:76px}
.badge{width:115px;height:60px;background:#dfe4ee;margin-bottom:12px}
.badge.small{width:75px;height:52px;background:#e5e5e5}
.foot-rule{position:absolute;left:111px;top:318px;width:978px;height:1px;background:#444}
.copyright{position:absolute;left:0;top:340px;width:1200px;text-align:center;font-size:14px}
</style>
</head>
<body>

<header class="site-header">
  <div class="brand"><span class="brand-mark"></span>SKILLPATH</div>
  <nav class="main-nav">
    <span class="active">HOME</span><span class="sep">|</span>
    <span>SKILL TRENDS</span><span class="sep">|</span>
    <span>SKILLS</span><span class="sep">|</span>
    <span>CAREER</span><span class="sep">|</span>
    <span>CONTACT US</span>
  </nav>
</header>

<section class="hero" role="img" aria-label="Digital human head made of glowing circuit lines and binary code on a dark blue background">
  <svg class="hero-arrow" style="left:68px" width="24" height="48" viewBox="0 0 24 48"><polyline points="22,2 2,24 22,46" fill="none" stroke="#fff" stroke-width="2"/></svg>
  <svg class="hero-arrow" style="left:1108px" width="24" height="48" viewBox="0 0 24 48"><polyline points="2,2 22,24 2,46" fill="none" stroke="#fff" stroke-width="2"/></svg>
  <h1 class="hero-title">SKILLPATH</h1>
  <p class="hero-sub">Your personal guide to the skill trends on the job marke</p>
  <div class="btn">Get started</div>
  <div class="dots"><i></i><i></i></div>
</section>

<section class="goal">
  <div class="frame-tl"></div>
  <div class="goal-photo" role="img" aria-label="Team of developers working together at computer screens in a brick-walled office"></div>
  <div class="frame-br"></div>
  <div class="goal-copy">
    <h2 class="heading">Main goal</h2>
    <p>We enable deep and unbiased analysis of the skill demands in the job market. Using deep learning techniques, we achieve understanding of job advertisements to extract the most relevant information for you. We combine these analysis with the most complete structural knowledge repositories to deliver analytics, discover trends and provide recommendations for personal professional development, as well as insightful job market overviews!</p>
    <div class="btn">Get started</div>
  </div>
</section>

<section class="ways" role="region" aria-label="Three different ways to proceed">
  <h2 class="heading">Three different ways to proceed</h2>
  <div class="card search-card">
    <div class="search-field"><span>Enter a skill</span><span>EN ⌄</span></div>
  </div>
  <div class="card ad-card">
    Your tasks:<br>
    as sales associate you are the first contact for our customers and handle requests <span class="tag">Advice</span><br>
    and acquiring new clients<br>
    Handling requests and sending information material<br>
    Preparing offers and tracking them until order<br>
    Phone sales of our products<br>
    Acquiring new clients<br>
    Close work with all teams of the company, intensive<br>
    <span class="tag">Communication</span><span class="tag">Communication</span> with the area <span class="tag">Customer service</span>
  </div>
  <div class="card chart-card">
    <svg width="314" height="111" viewBox="0 0 314 111" font-family="Courier New, monospace" font-size="5.5" font-weight="700" fill="#222">
      <text x="8" y="8">Project</text><text x="8" y="14">Management</text><text x="8" y="20">Skills</text>
      <circle cx="62" cy="13" r="2" fill="#d62828"/><text x="66" y="15">Pedagogy</text>
      <circle cx="128" cy="7" r="2" fill="#1f77b4"/><text x="132" y="8">Use of</text><text x="132" y="14">Office</text><text x="132" y="20">Software</text>
      <circle cx="188" cy="7" r="2" fill="#9b59b6"/><text x="192" y="8">Alternative</text><text x="192" y="14">Teaching</text><text x="192" y="20">Techniques</text>
      <circle cx="258" cy="7" r="2" fill="#2ca02c"/><text x="262" y="8">Human</text><text x="262" y="14">Resource</text><text x="262" y="20">Management</text>
      <line x1="8" y1="96" x2="306" y2="96" stroke="#999" stroke-width=".6"/>
      <polyline fill="none" stroke="#ff8c00" stroke-width="1" points="8,42 30,46 50,44 70,50 90,48 110,52 130,50 150,54 170,52 190,55 210,53 230,56 250,54 270,55 290,52 306,40"/>
      <polyline fill="none" stroke="#1f77b4" stroke-width="1" points="8,58 30,60 50,62 70,58 90,64 110,62 130,66 150,60 170,64 190,62 210,66 230,63 250,66 270,62 290,64 306,60"/>
      <polyline fill="none" stroke="#d62828" stroke-width="1" points="8,70 30,68 50,72 70,70 90,74 110,70 130,73 150,71 170,74 190,72 210,75 230,73 250,74 270,73 290,72 306,71"/>
      <polyline fill="none" stroke="#9b59b6" stroke-width="1" points="8,78 30,80 50,79 70,82 90,80 110,83 130,81 150,84 170,82 190,84 210,83 230,85 250,84 270,85 290,83 306,82"/>
      <polyline fill="none" stroke="#2ca02c" stroke-width="1" points="8,86 30,87 50,86 70,88 90,87 110,89 130,88 150,89 170,88 190,89 210,88 230,89 250,88 270,88 290,84 306,52"/>
      <text x="18" y="106">2015</text><text x="63" y="106">2016</text><text x="108" y="106">2017</text><text x="153" y="106">2018</text><text x="198" y="106">2019</text><text x="243" y="106">2020</text><text x="288" y="106">2021</text>
    </svg>
  </div>
</section>

<section class="intro">
  <h2 class="heading">We introduce our application</h2>
  <div class="challenges">
    <h3 class="heading">Challenges</h3>
    <p>Choosing the correct occupation plays an increasingly important role in our lives. Nowadays we consider an occupation as one of our fundamental rights. Yet, with the complexity of the modern technologies and job markets it is challenging to guarantee equal access to the market for everyone.</p>
    <p>The challenges include the knowledge of languages, personal traits, different understanding of requirements and different assessments of personal strengths. On the other end, business owners and recruitment professionals invest lots of effort to find suitable candidates for their job openings. How do we improve the situation, overcome the challenges and enable efficient, unbiased analysis of job advertisements without the need to change the existing practices?</p>
  </div>
  <div class="intro-photo" style="left:600px;top:169px;width:600px;height:528px;background:linear-gradient(165deg,#15181d 0%,#262a31 35%,#4a3f36 60%,#9a6a40 85%,#b07a48 100%)" role="img" aria-label="Hands typing on a laptop beside a monitor showing code under a desk lamp"></div>
  <div class="intro-photo" style="left:0;top:697px;width:600px;height:525px;background:linear-gradient(135deg,#24356e 0%,#5a6fc4 35%,#c7b3e6 55%,#7f8fd6 75%,#2b3a7a 100%)" role="img" aria-label="White robotic hand reaching towards a laptop keyboard in blue light"></div>
  <div class="method">
    <h3 class="heading">How we do this</h3>
    <p>We employ machine learning. Machines do not have personal preferences or biases. The impressive progress of natural language processing and deep neural networks power our algorithms to precisely recognize and extract the most important pieces of information. We use manually designed ontologies that set the frames of the analysis and guide the machine in this process. However, machines (and also we ourselves) still miss a lot of background information about our complex professional world -- no one is perfect (yet). To fill in this gap we use the most complete structural knowledge sources to serve as background knowledge and provide additional information about the subject area. The combination of these two methodologies yields human-like processing results at huge scales. This allows us to aggregate data, provide deep insights, and identify novelties in the ever evolving job market.</p>
  </div>
</section>

<section class="about">
  <h2 class="heading">About us</h2>
  <div class="about-text">
    <p>This application is a free social project powered by 3 enthusiast. We are experts in Natural Language Processing and Semantic Web with a record of 50+ scientific publications at top conferences and journals (<a href="#">https://research.skillpath-demo.org/profile/a-team</a>, <a href="#">https://research.skillpath-demo.org/profile/b-team</a>). We also have training and work experience in HR, and, most importantly passion for the job market. We all have migrant backgrounds and we know how difficult and important it might be to find your place in any new professional environment. Therefore, we strive to provide better professional opportunities, equal access and fair treatment for everyone.</p>
    <p>At the moment the project is completely funded by us. This not only includes the maintenance and further development, but also the costs of the infrastructure. If you like it and want us to continue, please, support us. Your every donation counts.</p>
  </div>
  <div class="member" style="left:111px">
    <div class="member-photo" style="background:linear-gradient(180deg,#f3f3f3,#dcdfe3 60%,#6f93b5)" role="img" aria-label="Portrait of a team member in a blue t-shirt"></div>
    <h4>JOHN DOE</h4>
    <p>Lorem ipsum dolor sit amet, consectetur adipiscing elit, sed do eiusmod tempor incididunt ut labore et dolore magna aliqua.</p>
    <div class="socials"><i></i><i></i><i></i><i></i></div>
  </div>
  <div class="member" style="left:443px">
    <div class="member-photo" style="background:linear-gradient(180deg,#eef0f2,#d3d6da 55%,#4a6688)" role="img" aria-label="Portrait of a team member in a checked shirt"></div>
    <h4>JOHN DOE</h4>
    <p>Lorem ipsum dolor sit amet, consectetur adipiscing elit, sed do eiusmod tempor incididunt ut labore et dolore magna aliqua.</p>
    <div class="socials"><i></i><i></i><i></i><i></i></div>
  </div>
  <div class="member" style="left:774px">
    <div class="member-photo" style="background:linear-gradient(180deg,#5f87b8,#6f96c4 50%,#9fbde0)" role="img" aria-label="Portrait of a team member in a light blue shirt"></div>
    <h4>JOHN DOE</h4>
    <p>Lorem ipsum dolor sit amet, consectetur adipiscing elit, sed do eiusmod tempor incididunt ut labore et dolore magna aliqua.</p>
    <div class="socials"><i></i><i></i><i></i><i></i></div>
  </div>
  <div class="donate">DONATE</div>
</section>

<footer class="site-footer">
  <div class="foot-brand"><div class="brand-mark"></div><span>SKILLPATH</span></div>
  <div class="foot-col links">
    <h5>QUICK LINKS</h5>
    <ul><li>Home</li><li>Skill trends</li><li>Skills</li><li>Career</li><li>Contact Us</li></ul>
  </div>
  <div class="foot-col newsletter">
    <h5>SIGN FOR NEWSLETTER</h5>
    <div class="field">Enter Email Adress</div>
    <div class="subscribe">SUBSCRIBE</div>
    <span class="round"></span><span class="round"></span>
  </div>
  <div class="foot-col powered">
    <h5>POWERED BY</h5>
    <div class="badge" role="img" aria-label="Partner badge"></div>
    <div class="badge small" role="img" aria-label="Partner badge"></div>
  </div>
  <div class="foot-rule"></div>
  <div class="copyright">Copyright © 2021 | All Rights Reserved</div>
</footer>

</body>
</html>
```